Business card design Needed for new logo / Construction business, home extensions and new builds

We need a business card design using our new logo files which i will attach to this project :)

We are a small construction business specialising in home extensions, new builds and property development. We are very ambitious and would appreciate professional and elegant designs for our new business card.

Very serious about using the services on MakerQuarry and recently acquired our new logo from here :)

Please get involved, i will feedback when i can as i am very busy but can respond daily, thanks

Target Market(s)

People that want to build onto their houses, new building developments or adding too their existing property

Industry/Entity Type

Construction

Contact Information for Business Card

Renwick Tolliver Construction, Lionel Ashby (Managing Director), Tel 07822254961, email - info@renwick-tolliver, www.renwick-tolliver.co.uk

Colors

Designer to choose colors to be used in the design.

Requirements
Must have
• I like a deep grey on the back please. A lot of you have provided black from and back, try mixing things up a little. The black looks cool 😎 Thanks

```html
<!DOCTYPE html>
<html lang="en">
<head>
<meta charset="utf-8">
<title>Renwick Tolliver Construction – Business Card</title>
<link href="https://fonts.googleapis.com/css2?family=Open+Sans:wght@400;600;700&display=swap" rel="stylesheet">
<style>
  :root {
    --page-bg: #18181a;
    --card-front: #1f1f23;
    --card-back-light: #a3a6ab;
    --card-back-dark: #7f8288;
    --gold: #d7a22e;
    --gold-deep: #a8781a;
    --gold-light: #f0cf72;
    --silver: #c9cacd;
    --white: #f2f2f2;
    --mark-faint: #2c2924;
  }
  * { margin: 0; padding: 0; box-sizing: border-box; }
  html, body { width: 1200px; height: 780px; overflow: hidden; }
  body {
    background: var(--page-bg);
    font-family: "Open Sans", Arial, sans-serif;
    position: relative;
  }
  .card {
    position: absolute;
    top: 222px;
    width: 520px;
    height: 336px;
    border-radius: 4px;
    overflow: hidden;
    box-shadow: 0 14px 30px rgba(0,0,0,.45);
  }
  /* ---------- front ---------- */
  .card-front { left: 50px; background: var(--card-front); }
  .brand {
    position: absolute; left: 34px; top: 30px;
    display: flex; align-items: center; gap: 10px;
  }
  .brand-square { width: 22px; height: 22px; background: var(--gold); }
  .brand-name {
    color: var(--gold); font-weight: 600; font-size: 13px;
    letter-spacing: 1.4px; text-transform: uppercase; line-height: 1.25;
  }
  .address {
    position: absolute; left: 34px; top: 92px;
    color: var(--white); font-size: 13.5px; line-height: 1.45;
  }
  .contacts {
    position: absolute; left: 34px; top: 160px;
    list-style: none; color: var(--white); font-size: 13.5px; line-height: 1.5;
  }
  .contacts li { display: flex; align-items: center; gap: 9px; }
  .contacts svg { width: 13px; height: 13px; fill: var(--gold); flex: none; }
  .brand-mark-faint {
    position: absolute; right: 40px; bottom: 34px;
    width: 250px; height: 230px;
    background: linear-gradient(150deg, #2a2a2e 0%, var(--mark-faint) 60%, #332c22 100%);
    border-radius: 6px;
  }
  .person {
    position: absolute; right: 48px; bottom: 92px; text-align: right;
  }
  .person-name { font-size: 30px; font-weight: 600; line-height: 1.1; }
  .person-first { color: var(--silver); }
  .person-last { color: var(--gold); }
  .person-role { color: var(--white); font-size: 15px; margin-top: 4px; }
  .gold-steps { position: absolute; right: 0; bottom: 56px; width: 36px; }
  .gold-steps span {
    display: block; height: 9px; margin-bottom: 3px; margin-left: auto;
    background: linear-gradient(180deg, var(--gold-light), var(--gold) 50%, var(--gold-deep));
  }
  .gold-steps span:nth-child(1) { width: 24px; }
  .gold-steps span:nth-child(2) { width: 30px; }
  .gold-steps span:nth-child(3) { width: 36px; }
  .gold-steps span:nth-child(4) { width: 30px; }
  .gold-steps span:nth-child(5) { width: 24px; }
  /* ---------- back ---------- */
  .card-back { left: 630px; }
  .back-pattern {
    position: absolute; inset: 0;
    background: linear-gradient(125deg, var(--card-back-dark) 0%, var(--card-back-light) 55%, #c4c6ca 100%);
  }
  .back-brand {
    position: absolute; right: 28px; bottom: 26px;
    display: flex; align-items: center; gap: 6px;
  }
  .back-brand-square { width: 12px; height: 12px; background: var(--white); }
  .back-brand-name {
    color: var(--white); font-size: 8px; font-weight: 600;
    letter-spacing: .8px; text-transform: uppercase;
  }
</style>
</head>
<body>
  <section class="card card-front" aria-label="Business card front">
    <div class="brand">
      <span class="brand-square"></span>
      <span class="brand-name">Renwick Tolliver<br>Construction</span>
    </div>
    <p class="address">Halden Lane, Westbury Heath<br>Ashcombe, AC4 7RT</p>
    <ul class="contacts">
      <li><svg viewBox="0 0 24 24"><path d="M6.6 10.8a15.2 15.2 0 0 0 6.6 6.6l2.2-2.2a1 1 0 0 1 1-.25 11.4 11.4 0 0 0 3.6.57 1 1 0 0 1 1 1V20a1 1 0 0 1-1 1A17 17 0 0 1 3 4a1 1 0 0 1 1-1h3.5a1 1 0 0 1 1 1c0 1.25.2 2.45.57 3.57a1 1 0 0 1-.25 1z"/></svg>0782 225 4961</li>
      <li><svg viewBox="0 0 24 24"><path d="M12 2a10 10 0 1 0 0 20 10 10 0 0 0 0-20zm6.9 6h-2.9a15.6 15.6 0 0 0-1.4-3.6A8 8 0 0 1 18.9 8zM12 4c.8 1.2 1.5 2.5 1.9 4h-3.8c.4-1.5 1.1-2.8 1.9-4zM4.3 14a8 8 0 0 1 0-4h3.4a16 16 0 0 0 0 4zm.8 2h2.9c.3 1.3.8 2.5 1.4 3.6A8 8 0 0 1 5.1 16zM8 8H5.1a8 8 0 0 1 4.3-3.6C8.8 5.5 8.3 6.7 8 8zm4 12c-.8-1.2-1.5-2.5-1.9-4h3.8c-.4 1.5-1.1 2.8-1.9 4zm2.3-6H9.7a14.7 14.7 0 0 1 0-4h4.6a14.7 14.7 0 0 1 0 4zm.3 5.6c.6-1.1 1.1-2.3 1.4-3.6h2.9a8 8 0 0 1-4.3 3.6zm1.7-5.6a16 16 0 0 0 0-4h3.4a8 8 0 0 1 0 4z"/></svg>info@renwick-tolliver.co.uk</li>
      <li><svg viewBox="0 0 24 24"><path d="M3 5h18a1 1 0 0 1 1 1v12a1 1 0 0 1-1 1H3a1 1 0 0 1-1-1V6a1 1 0 0 1 1-1zm9 7.2L4.4 7H4v1.1l8 5.4 8-5.4V7h-.4z"/></svg>www.renwick-tolliver.co.uk</li>
    </ul>
    <div class="brand-mark-faint" role="img" aria-label="Large faint brand mark decoration in dark bronze tones"></div>
    <div class="person">
      <p class="person-name"><span class="person-first">Lionel</span> <span class="person-last">Ashby</span></p>
      <p class="person-role">Managing Director</p>
    </div>
    <div class="gold-steps" aria-hidden="true"><span></span><span></span><span></span><span></span><span></span></div>
  </section>

  <section class="card card-back" aria-label="Business card back">
    <div class="back-pattern" role="img" aria-label="Tiled repeating pattern of the brand mark in glossy silver on deep grey"></div>
    <div class="back-brand">
      <span class="back-brand-square"></span>
      <span class="back-brand-name">Renwick Tolliver Construction</span>
    </div>
  </section>
</body>
</html>
```